Dental Practice Billboard Design

We are a newer dental practice in need of a simple but appealing billboard for our growing dental practice to attract new patients. The practice is owned by husband and wife dentists and is family friendly in a small town in Kentucky. We try to be very friendly and caring to our patients. Would prefer a blue background for the billboard and our tooth logo to be prominent. We are partial to the Patua One font used in the image below but please feel free to tweak it as you deem necessary. The shape of the uppercase D and lowercase g are why we like that font, so fonts with a similarly shaped “D” and “g” would work as well. Please include our phone number (555) 847-1390. Please see our website Harlowbrookdentistry.example for more info on the practice if needed. Thank you! Looking forward to seeing your creation.
Updates

The dimensions will be 12ft x 24ft (3.6576m x 7.3152m). Apologies for not including this in the original prompt. Thank you all for your submissions.

Industry/Entity Type

Dental

Font styles to use
Other font styles liked:
• Patua One

Colors
0054AA
0677BA
7BADD7
CADEEF
E8F1F8
0094D4
00A9DD
6FCCEA
C7EBF8
E9F6FB
00AB8E
00BBA5
67D7C9
C6EFE9
E9F9F6
59FF00
82FF00
B8FF75
E3FFCB
F4FFEA

Requirements
Must have
• Phone number, website, Logo, Practice name “Harlow Brook Dentistry”
Should not have
• A tagline or slogan

```html
<!DOCTYPE html>
<html lang="en">
<head>
<meta charset="utf-8">
<title>Harlow Brook Dentistry Billboard</title>
<link rel="stylesheet" href="https://fonts.googleapis.com/css2?family=Anton&family=Montserrat:wght@700&family=Patua+One&display=swap">
<style>
  :root {
    --navy: #243a87;
    --green: #5db843;
    --white: #ffffff;
    --stroke-blue: #1f3278;
    --backdrop: #eef1f5;
  }
  * { margin: 0; padding: 0; box-sizing: border-box; }
  html, body {
    width: 1200px;
    height: 1000px;
    overflow: hidden;
    background: var(--backdrop);
  }
  .billboard {
    position: absolute;
    left: 0;
    top: 197px;
    width: 1200px;
    height: 605px;
  }
  .billboard__main {
    position: absolute;
    inset: 0 0 122px 0;
    background: var(--navy);
  }
  .services {
    position: absolute;
    top: 58px;
    font-family: "Montserrat", sans-serif;
    font-weight: 700;
    list-style: none;
  }
  .services--left { left: 80px; }
  .services--right { left: 888px; }
  .services__title {
    color: var(--green);
    font-size: 22px;
    line-height: 32px;
  }
  .services__item {
    color: var(--white);
    font-size: 22px;
    line-height: 32px;
    display: flex;
    align-items: center;
    gap: 6px;
  }
  .services__item::before {
    content: "";
    width: 10px;
    height: 10px;
    border-radius: 50%;
    border: 2px solid var(--white);
    flex: none;
  }
  .brand-mark {
    position: absolute;
    left: 0;
    right: 0;
    top: 80px;
    display: flex;
    flex-direction: column;
    align-items: center;
    gap: 16px;
  }
  .brand-mark__dot {
    width: 120px;
    height: 120px;
    border-radius: 50%;
    background: var(--green);
  }
  .brand-mark__name {
    font-family: "Patua One", serif;
    color: var(--white);
    font-size: 26px;
  }
  .practice-name {
    position: absolute;
    left: 0;
    right: 0;
    top: 298px;
    text-align: center;
    font-family: "Patua One", serif;
    font-weight: 400;
    color: var(--white);
    font-size: 96px;
    line-height: 106px;
  }
  .divider {
    position: absolute;
    left: 95px;
    width: 1008px;
    top: 414px;
    height: 2px;
    background: linear-gradient(90deg, transparent, rgba(255,255,255,0.85) 15%, rgba(255,255,255,0.85) 85%, transparent);
  }
  .website {
    position: absolute;
    left: 0;
    right: 0;
    top: 422px;
    text-align: center;
    font-family: "Patua One", serif;
    color: var(--green);
    font-size: 34px;
    line-height: 44px;
  }
  .call-band {
    position: absolute;
    left: 0;
    right: 0;
    bottom: 0;
    height: 122px;
    background: var(--green);
    display: flex;
    align-items: center;
    justify-content: center;
  }
  .call-band__text {
    font-family: "Anton", sans-serif;
    font-size: 98px;
    line-height: 1;
    color: var(--white);
    -webkit-text-stroke: 8px var(--stroke-blue);
    paint-order: stroke fill;
    letter-spacing: 1px;
  }
</style>
</head>
<body>
  <section class="billboard">
    <div class="billboard__main">
      <ul class="services services--left">
        <li class="services__title">Our Services</li>
        <li class="services__item">Crowns</li>
        <li class="services__item">Root Canals</li>
        <li class="services__item">Extractions</li>
        <li class="services__item">Implants</li>
        <li class="services__item">Bridges</li>
        <li class="services__item">Clear Aligner</li>
      </ul>

      <div class="brand-mark">
        <span class="brand-mark__dot"></span>
        <span class="brand-mark__name">Harlow Brook Dentistry</span>
      </div>

      <ul class="services services--right">
        <li class="services__title">Our Services</li>
        <li class="services__item">Veneers</li>
        <li class="services__item">Whitening</li>
        <li class="services__item">Fillings</li>
        <li class="services__item">Cleanings</li>
        <li class="services__item">Dentures</li>
        <li class="services__item">Overdentures</li>
      </ul>

      <h1 class="practice-name">Harlow Brook Dentistry</h1>
      <div class="divider"></div>
      <p class="website">Harlowbrookdentistry.example</p>
    </div>

    <div class="call-band">
      <p class="call-band__text">CALL TODAY! (555) 847-1390</p>
    </div>
  </section>
</body>
</html>
```